RW Holloway LLC Business Card - Civil Engineering & Consulting Firm

We need a Business Card that is elegant, and masculine.  It is our Professional Civil Engineering & Consulting Company located in San Antonio TX (Not s construction or builder firm- no gears & no tool images please). We provide civil engineering services including  commercial site plans, grading and drainage plans, utility plans, hydraulics and hydrology, land planning, utility coordination, and other general civil engineering services related to commercial and residential development.
We have 2 existing Logos. We would like to convey reliability, strength, trustworthiness and attention to detail.  Blues and orange tones as per logo We are OK with the use of a darker blue in the mix.  We have 2 logo versions - Full Company Name Logo to go on the back of card, & Small Icon Logo for the front w/ personal Info.

Target Market(s)
Architects, Real Estate Developers, Other Strctural Engineers, Surveyers, General Contractors
Industry/Entity Type
Professional Civil Engineering
Contact Information for Business Card
Name, Position, Address, Cell & Office #, email, and company website
Font styles to use
Other font styles liked:
- Avian
Requirements
Should not have
- No Tools, No Gears, no Cranes, or Construction Equipment.

```html
<!DOCTYPE html>
<html lang="en">
<head>
<meta charset="utf-8">
<title>RW Holloway LLC — Business Card</title>
<link rel="stylesheet" href="https://fonts.googleapis.com/css2?family=Montserrat:wght@400;500;700&display=swap">
<style>
  :root{
    --stage:#3a3a3a;
    --card:#171717;
    --blue:#6fa6dc;
    --orange:#f0922b;
    --white:#f2f2f2;
    --muted:#9a9a9a;
  }
  *{box-sizing:border-box;margin:0;padding:0}
  html,body{width:1200px;height:801px;overflow:hidden}
  body{
    background:var(--stage);
    font-family:"Montserrat",sans-serif;
    position:relative;
  }
  .card{
    position:absolute;top:246px;width:540px;height:309px;
    background:var(--card);
    border-bottom:2px solid var(--blue);
    overflow:hidden;
  }
  .card-front{left:40px}
  .card-back{left:620px}

  /* front: personal info */
  .front-brand{
    position:absolute;top:34px;right:36px;
    display:flex;align-items:center;gap:10px;
    color:var(--blue);font-weight:500;font-size:22px;letter-spacing:2px;
  }
  .brand-square{width:12px;height:12px;background:var(--orange)}
  .front-rule{position:absolute;top:98px;left:150px;right:36px;height:1px;background:var(--blue)}
  .address{
    position:absolute;top:116px;right:36px;text-align:right;
    color:var(--white);font-size:13px;line-height:19px;
  }
  .person{position:absolute;left:36px;top:176px}
  .person-name{color:var(--blue);font-weight:700;font-size:18px;letter-spacing:.5px}
  .person-role{color:var(--white);font-size:13px;margin-top:2px}
  .person-rule{width:190px;height:1px;background:var(--blue);margin:8px 0 8px}
  .contacts{list-style:none;color:var(--white);font-size:12px;line-height:18px}
  .contacts li{display:flex;align-items:center;gap:8px}
  .contacts svg{width:11px;height:11px;flex:none}

  /* back: brand */
  .back-decor{
    position:absolute;left:0;top:0;bottom:0;width:150px;
    background:linear-gradient(100deg,#0e0e0e 0%,#3c3c3c 45%,#bdbdbd 100%);
    opacity:.85;
  }
  .back-brand{
    position:absolute;left:190px;right:30px;top:0;bottom:0;
    display:flex;align-items:center;justify-content:center;gap:12px;
    color:var(--blue);font-weight:500;font-size:30px;letter-spacing:3px;
  }
</style>
</head>
<body>

<section class="card card-front" aria-label="Business card front">
  <div class="front-brand"><span class="brand-square"></span>RW Holloway LLC</div>
  <div class="front-rule"></div>
  <address class="address" style="font-style:normal">1180 Harbor Crest Drive<br>Bayview CA 90412</address>

  <div class="person">
    <p class="person-name">DANIEL CARVER</p>
    <p class="person-role">President</p>
    <div class="person-rule"></div>
    <ul class="contacts">
      <li><svg viewBox="0 0 12 12"><rect x="3" y="1" width="6" height="10" rx="1" fill="none" stroke="var(--orange)" stroke-width="1.4"/></svg>555-310-4182</li>
      <li><svg viewBox="0 0 12 12"><path d="M2 3c0 4 3 7 7 7l1.5-1.5-2-2-1.2 1C5.8 6.8 5.2 6.2 4.5 4.7l1-1.2-2-2z" fill="var(--orange)"/></svg>555-310-4190</li>
      <li><svg viewBox="0 0 12 12"><rect x="1" y="2.5" width="10" height="7" fill="var(--orange)"/><path d="M1 2.5l5 4 5-4" fill="none" stroke="var(--card)" stroke-width="1"/></svg>info@rwholloway.com</li>
      <li><svg viewBox="0 0 12 12"><circle cx="6" cy="6" r="5" fill="var(--orange)"/><path d="M1 6h10M6 1c-2 3-2 7 0 10M6 1c2 3 2 7 0 10" fill="none" stroke="var(--card)" stroke-width=".8"/></svg>www.rwholloway.com</li>
    </ul>
  </div>
</section>

<section class="card card-back" aria-label="Business card back">
  <div class="back-decor" role="img" aria-label="Large monochrome brand symbol decoration"></div>
  <div class="back-brand"><span class="brand-square"></span>RW Holloway LLC</div>
</section>

</body>
</html>
```